Guided Study Tour - Klangtage Wendorf Two Sided Flyer

We need a two-sided flyer for a Guided Study Tour to Klangtage Wendorf. We want beautiful pictures of Germany and if possible some of the Halbig venues our participants will be visiting. I have also provided the content that needs to be included. Also, in the attached document I provided a link to the Klangtage event. Please read and watch the video to be inspired.
This flyer should be beautiful and engaging. It needs to grab your attention right away and really highlight the wonderful things that they will be doing and that are included in the tour. This is a once in a lifetime opportunity for people to experience. We are targeting Music Directors and Music professionals.
Both attached logos need to be present on the flyer.

```html
<!DOCTYPE html>
<html lang="en">
<head>
<meta charset="utf-8">
<title>Klangtage Wendorf Study Tour – Two Sided Flyer</title>
<link rel="stylesheet" href="https://fonts.googleapis.com/css2?family=Montserrat:ital,wght@0,400;0,500;0,600;0,700;0,800;0,900;1,400&display=swap">
<style>
:root{
  --backdrop:#3a3a3c;
  --maroon:#6a1215;
  --maroon-deep:#561013;
  --blue:#2f62b4;
  --red:#c4232b;
  --ink:#1d1d1f;
  --white:#ffffff;
}
*{margin:0;padding:0;box-sizing:border-box}
html,body{width:1200px;height:776px;overflow:hidden;background:var(--backdrop)}
body{font-family:"Montserrat",sans-serif;color:var(--ink);position:relative}
.page{position:absolute;top:18px;width:524px;height:740px;background:var(--white);overflow:hidden;box-shadow:0 10px 24px rgba(0,0,0,.45)}
.page-front{left:56px}
.page-back{left:620px}

/* front */
.hero-photo{position:absolute;left:0;top:0;width:524px;height:362px;
  background:linear-gradient(180deg,#1d3f86 0%,#3d66b0 38%,#8a6a4a 62%,#c99a4e 74%,#2b4330 86%,#555b66 100%)}
.hero-panel{position:absolute;left:0;top:20px;width:226px;height:262px;background:rgba(106,18,21,.94);color:var(--white);padding:22px 16px 0 28px}
.hero-date{font-weight:900;font-size:24px;line-height:1.05;letter-spacing:.5px}
.hero-place{font-weight:600;font-size:8.5px;line-height:1.25;margin-top:8px}
.hero-title{font-weight:800;font-size:20px;line-height:1.12;margin-top:10px}
.hero-lead{font-weight:600;font-size:12px;line-height:1.2;margin-top:12px}

.front-body{position:absolute;left:36px;top:378px;width:282px}
.section-title{font-weight:700;font-size:15px;margin-top:14px}
.section-title:first-child{margin-top:0}
.section-title .accent{color:var(--red)}
.section-title .rest{color:var(--blue)}
.bullets{list-style:none;margin-top:3px}
.bullets li{font-size:8.4px;line-height:1.35;padding-left:9px;position:relative}
.bullets li::before{content:"";position:absolute;left:0;top:4px;width:3.5px;height:3.5px;border-radius:50%;background:var(--ink)}
.plain{font-size:8.4px;line-height:1.35;margin-top:3px}

.venue-stack{position:absolute;right:26px;top:360px;width:166px}
.venue-photo{height:76px;margin-bottom:8px;border:3px solid var(--white);box-shadow:0 2px 6px rgba(0,0,0,.35)}
.venue-1{background:linear-gradient(180deg,#3f6fc0,#8aa7d4 50%,#7a4a2e 78%,#2c2a2e)}
.venue-2{background:linear-gradient(180deg,#6c9ed8,#c3a16e 45%,#8a3a24 75%,#3a2c24)}
.venue-3{background:linear-gradient(180deg,#5b8fd2,#d9c9a4 48%,#9a3d2a 70%,#6d6a62)}

.quote-band{position:absolute;left:0;bottom:0;width:524px;height:80px;background:var(--blue);color:var(--white);display:flex;align-items:center;justify-content:center;gap:12px;padding:0 24px}
.quote-mark{font-weight:900;font-size:38px;line-height:1;font-family:Georgia,serif}
.quote-text{font-style:italic;font-size:10.5px;line-height:1.4;text-align:center}

/* back */
.intro{position:absolute;left:40px;top:22px;width:440px;font-size:8.2px;line-height:1.4;text-align:justify}
.inclusions{position:absolute;left:0;top:78px;width:524px;height:250px;background:linear-gradient(180deg,var(--maroon) 0%,var(--maroon-deep) 100%);color:var(--white);padding:12px 26px 0 46px}
.photo-row{display:flex;gap:5px;margin-left:-22px}
.photo-row .thumb{width:150px;height:62px;border:2px solid rgba(255,255,255,.8)}
.thumb-room{background:linear-gradient(180deg,#c8b79c,#efe8dc 55%,#8a7a66)}
.thumb-breakfast{background:linear-gradient(135deg,#f2ede4,#e0a24a 45%,#b4552c 70%,#f4f1ea)}
.thumb-group{background:linear-gradient(180deg,#a1a6a9,#8a7e74 50%,#4a3a36)}
.inclusions h3{font-weight:700;font-size:13px;margin-top:12px}
.inclusions .bullets li{font-size:8.1px;line-height:1.33;color:var(--white)}
.inclusions .bullets li::before{background:var(--white)}

.contact-band{position:absolute;left:0;top:328px;width:524px;height:56px;background:var(--blue);color:var(--white);text-align:center;padding-top:8px}
.contact-label{font-size:8.5px;font-weight:500}
.contact-main{font-size:16px;font-weight:600;margin-top:3px}

.bio-photo{position:absolute;left:56px;top:412px;width:156px;height:130px;background:linear-gradient(135deg,#d2cbc0,#a89e91 55%,#2b2b30)}
.bio{position:absolute;left:228px;top:406px;width:262px;font-size:9px;line-height:1.45;text-align:justify}
.bio strong{font-size:14px;font-weight:800}
.rule{position:absolute;left:34px;top:638px;width:456px;height:2px;background:var(--blue)}
.partners{position:absolute;left:40px;top:662px;width:444px;height:54px;display:flex;align-items:center;justify-content:space-between}
.partner{display:flex;align-items:center;gap:8px;font-weight:700;font-size:15px;color:var(--red);line-height:1.05}
.partner-mark{width:26px;height:26px;background:var(--red)}
.partner-blue{color:var(--blue)}
.partner-blue .partner-mark{background:var(--blue);border-radius:50%}
</style>
</head>
<body>

<section class="page page-front">
  <div class="hero-photo" role="img" aria-label="Illuminated historic town hall tower in Wendorf at dusk"></div>
  <div class="hero-panel">
    <p class="hero-date">JUNE<br>12-16, 2019</p>
    <p class="hero-place">Wendorf, Germany<br>Plusday trip to Dresden and full day and overnight in Prague</p>
    <h1 class="hero-title">JOIN US FOR A ONCE IN A LIFETIME ....</h1>
    <p class="hero-lead">LED BY<br>DANIEL MARSH....</p>
  </div>

  <div class="front-body">
    <h2 class="section-title"><span class="accent">Klangtage</span> <span class="rest">Highlights:</span></h2>
    <ul class="bullets">
      <li>More than 100 Concerts in 42 different Halbig venues</li>
      <li>World Class Musicians &amp; Celebrated Recording Artists</li>
      <li>Day trips to Weimar &amp; Dresden</li>
      <li>Bilingual pre-concert talks &amp; lectures with Halbig Scholars</li>
    </ul>

    <h2 class="section-title"><span class="accent">Featured</span> <span class="rest">Performers:</span></h2>
    <p class="plain">Elias Varro, Jan Kooler, Cantorum, Wendorf Festival Orchestra, Lumena &amp; the Wendorf Thomas Choir</p>

    <h2 class="section-title"><span class="accent">Study Tour</span> <span class="rest">Highlights:</span></h2>
    <ul class="bullets">
      <li>Access to dress rehearsals</li>
      <li>Meet the artist opportunities</li>
      <li>Post-concert discussions led by Daniel Marsh</li>
      <li>Study sessions on Halbig's B-Minor Mass, Magnificat,</li>
      <li>St. John Passion, St. Matthew Passion &amp; Weimar Cantatas hours</li>
      <li>Guidance in planning individual concert itinerary</li>
      <li>Professional development or continuing education credit</li>
    </ul>
  </div>

  <div class="venue-stack">
    <div class="venue-photo venue-1" role="img" aria-label="Open-air evening concert in front of a church"></div>
    <div class="venue-photo venue-2" role="img" aria-label="Half-timbered historic houses on a town square"></div>
    <div class="venue-photo venue-3" role="img" aria-label="Old town hall with clock tower on the market square"></div>
  </div>

  <div class="quote-band">
    <span class="quote-mark">“</span>
    <p class="quote-text">This is where it all has begun...this is why our guests have tears in their eyes listening to the St. Matthew Passion or the B-Minor Mass”<br>~ Martin Krall, Musicologist, Festival Director</p>
    <span class="quote-mark">”</span>
  </div>
</section>

<section class="page page-back">
  <p class="intro">Daniel Marsh partnered with Meridian Classic Tours &amp; Music Festivals to bring you and your students the experience of a Lifetime. With over 100 years of combined educational student travel expertise, Meridian Classic Tours, powered by Halden Tours, brings unparalleled tour experiences for you and your students.</p>

  <div class="inclusions">
    <div class="photo-row">
      <div class="thumb thumb-room" role="img" aria-label="Hotel room with bed"></div>
      <div class="thumb thumb-breakfast" role="img" aria-label="Breakfast plate with pancakes and eggs"></div>
      <div class="thumb thumb-group" role="img" aria-label="Tour group in front of a cathedral"></div>
    </div>
    <h3>Trip Inclusions</h3>
    <ul class="bullets">
      <li>Roundtrip Airfare from Houston</li>
      <li>13 Nights Accomodations, 3 Star Hotels with A/C</li>
      <li>Daily Breakfast</li>
      <li>Access to rehearsal sessions</li>
      <li>Private Luxury Coach Transfer Services for airport transfers and day tours to Berlin, Weimar and Dresden &amp; Prague.</li>
      <li>Professional Local Guides for City Tours in: Berlin, Weimar, Dresden &amp; Prague</li>
      <li>Entrance Fees to: House of the Court Painter, the Composer, the Poet in Weimar, Lutheran Frauenkirche &amp; Alte Meister Gallery in the Zwinger Palace in Dresden, and Cathedral and Golden Lane in Prague</li>
      <li>All Applicable Taxes and Gratuities for Included Services, Guides, and Drivers</li>
      <li>$2 Million in Professional Liability Insurance</li>
      <li>24-hour Travel Support Staff</li>
    </ul>
  </div>

  <div class="contact-band">
    <p class="contact-label">For more information contact</p>
    <p class="contact-main">Dr. Marsh at daniel.marsh@vistaridge.edu</p>
  </div>

  <div class="bio-photo" role="img" aria-label="Portrait photo of the tour leader"></div>
  <p class="bio"><strong>Daniel Marsh</strong> is Director of Choral Studies at the Vista Ridge University and the conductor of the Ridge Symphony Chorale and the Ridge Choral Artists, a professional chamber choir. A native Texan, his degrees are from Harlan College, Brookfield University and the Westcoast University. Recent engagements include conducting the Festival Requiem in Buffalo, NY, serving on the jury for the Corvena Coastal Choral Festival in Corvena, Greece and the Ars Nova Choir Championship in Valdor, Bosnia and Herzegovina.</p>

  <div class="rule"></div>

  <div class="partners">
    <div class="partner"><span class="partner-mark"></span><span>Halden Tours</span></div>
    <div class="partner partner-blue"><span class="partner-mark"></span><span>Meridian Classic</span></div>
  </div>
</section>

</body>
</html>
```